Need a developer to develop and design my virtual employee recruitment solution website.

I need the entire website developed, from the design, the navigation, the contents of the website, etc. I need a professional looking website yet have that modern look. You can suggest the best fonts, color combinations to use. I need the site to be SEO friendly. I also want high quality stock photos to be used on the website. I wanted to achieve a similar website like this https://remotehelperpool.example/.

Target Market(s)

Ecommerce Entrepreneurs, Businessmen, Cartwell and Bazorra Sellers.

Industry/Entity Type

Professional Service

Coding

Coded - Design and coding required

Number of Pages Required

5+ page

Font styles to use
Sans Serif

Requirements
Must have
• I wanted it to have pages like this https://remotehelperpool.example/
Nice to have
• open for any recommendation you can suggest
Should not have
• Cannot think of any. You can suggest your own here

```html
<!DOCTYPE html>
<html lang="en">
<head>
<meta charset="utf-8">
<title>HavenStaff – Virtual Employee Recruitment Services</title>
<link href="https://fonts.googleapis.com/css2?family=Montserrat:wght@400;500;600;700&family=Lato:wght@400;700&display=swap" rel="stylesheet">
<style>
:root{
  --blue:#1565d0;
  --blue-deep:#0a3f94;
  --orange:#fb840f;
  --navy:#0f1b2b;
  --ink:#1b1b1b;
  --grey:#555;
  --black-bar:#050505;
  --ring:#d9e5f5;
  --white:#fff;
}
*{margin:0;padding:0;box-sizing:border-box}
html,body{width:1200px;height:3322px;overflow:hidden;background:var(--white)}
body{position:relative;font-family:"Montserrat",sans-serif;color:var(--ink)}
.abs{position:absolute}

/* header */
.topbar{left:0;top:0;width:1200px;height:97px;background:var(--white)}
.contact-item{top:40px;display:flex;align-items:center;gap:10px;font-size:17px}
.contact-item.phone{left:617px;font-weight:600}
.contact-item.mail{left:825px}
.navband{left:0;top:97px;width:1200px;height:64px;background:linear-gradient(90deg,#2a7fe0,var(--blue) 60%,#0b4fb8)}
.nav{left:0;top:97px;height:64px;width:1200px}
.nav a{position:absolute;top:24px;color:var(--white);font-size:14px;font-weight:700;text-decoration:none;letter-spacing:.2px}
.nav a.active::after{content:"";position:absolute;left:-8px;right:-8px;top:38px;height:4px;background:var(--white)}
.logo-disc{left:78px;top:-6px;width:162px;height:162px;border-radius:50%;background:var(--white)}
.logo-name{left:78px;top:62px;width:162px;text-align:center;font-size:22px;font-weight:700;color:var(--blue)}

/* hero */
.hero{left:0;top:161px;width:1200px;height:601px;background:linear-gradient(180deg,#5f7384 0%,#a9b7c0 30%,#cfd2cc 55%,#e7e2d8 100%)}
.hero-title{left:0;top:262px;width:1200px;text-align:center;color:var(--white);font-weight:500;line-height:1.1}
.hero-title .l1{font-size:46px;display:block}
.hero-title .l2{font-size:54px;display:block}
.btn-quote{left:502px;top:391px;width:220px;height:54px;background:var(--orange);color:var(--white);font-size:16px;font-weight:700;display:flex;align-items:center;justify-content:center}
.arrow{top:436px}

/* intro */
.intro{left:140px;top:872px;width:920px;text-align:center;color:var(--grey);font-size:18.5px;line-height:31px}
.intro p+p{margin-top:15px}

/* split blocks */
.photo-agent{left:0;top:1139px;width:589px;height:486px;background:linear-gradient(135deg,#f4f3f1,#dcdad6 60%,#c9c4bd)}
.benefits{left:589px;top:1139px;width:611px;height:486px;background:var(--orange);color:var(--white)}
.benefits h2{position:absolute;left:72px;top:92px;font-size:26px;font-weight:700;line-height:28px}
.benefits ul{position:absolute;left:80px;top:164px;list-style:none;font-family:"Lato",sans-serif;font-size:17.5px;line-height:30px;width:470px}
.benefits li{position:relative;padding-left:28px;margin-bottom:10px}
.benefits li svg{position:absolute;left:0;top:8px}
.who{left:0;top:1625px;width:590px;height:540px;background:var(--navy);color:var(--white)}
.who h2{position:absolute;left:87px;top:68px;font-size:27px;font-weight:700;line-height:35px}
.who .copy{position:absolute;left:91px;top:151px;width:452px;font-family:"Lato",sans-serif;font-size:15.5px;line-height:25px}
.who .copy p{margin-bottom:11px}
.photo-beach{left:590px;top:1625px;width:610px;height:540px;background:linear-gradient(180deg,#b8d3e4 0%,#7fb6d3 30%,#e4e7e8 55%,#f1efec 100%)}

/* why */
.why-title{left:0;top:2238px;width:1200px;text-align:center;font-size:30px;font-weight:700}
.bar{height:64px;background:var(--black-bar);color:var(--white);font-size:14.5px;font-weight:700;line-height:21px;display:flex;align-items:center}
.bar.left{left:84px;width:430px;justify-content:flex-start}
.bar.left .label{width:197px;text-align:right}
.bar.left svg{margin-left:16px}
.bar.right{left:690px;width:444px}
.bar.right svg{margin-left:174px}
.bar.right .label{margin-left:24px}
.bar.active{background:var(--blue)}
.circle-glow{left:337px;top:2301px;width:520px;height:520px;border-radius:50%;background:radial-gradient(circle,rgba(60,120,210,.25) 40%,rgba(60,120,210,0) 70%)}
.circle-ring{left:358px;top:2322px;width:478px;height:478px;border-radius:50%;background:var(--ring)}
.circle-core{left:371px;top:2335px;width:452px;height:452px;border-radius:50%;background:linear-gradient(180deg,var(--blue) 0%,var(--blue-deep) 100%);color:var(--white);text-align:center}
.circle-core svg{position:absolute;left:184px;top:92px}
.circle-core h3{position:absolute;left:0;top:205px;width:452px;font-size:23px;font-weight:700}
.circle-core p{position:absolute;left:70px;top:247px;width:312px;font-size:15px;line-height:35px}

/* footer */
.footer{left:0;top:2907px;width:1200px;height:415px;background:var(--blue);color:var(--white)}
.footer h4{position:absolute;top:73px;font-size:22px;font-weight:500}
.footer ul{position:absolute;top:132px;list-style:none;font-family:"Lato",sans-serif;font-size:15.5px;line-height:29.5px}
.social{position:absolute;left:832px;top:137px;display:flex;gap:5px}
.social span{width:43px;height:43px;border:2px solid var(--white);border-radius:50%}
.rule{position:absolute;left:155px;top:355px;width:897px;height:1px;background:rgba(255,255,255,.4)}
.copyright{position:absolute;left:0;top:370px;width:1200px;text-align:center;font-family:"Lato",sans-serif;font-size:13.5px}
</style>
</head>
<body>

<header>
  <div class="abs topbar"></div>
  <div class="abs navband"></div>
  <div class="abs logo-disc"></div>
  <div class="abs logo-name">HavenStaff</div>
  <div class="abs contact-item phone">
    <svg width="26" height="26" viewBox="0 0 24 24" fill="none" stroke="#1565d0" stroke-width="2"><path d="M5 3h4l2 5-3 2a12 12 0 0 0 6 6l2-3 5 2v4a2 2 0 0 1-2 2A18 18 0 0 1 3 5a2 2 0 0 1 2-2z"/></svg>
    (555) 014 2290
  </div>
  <div class="abs contact-item mail">
    <svg width="30" height="22" viewBox="0 0 30 22"><rect width="30" height="22" fill="#1565d0"/><path d="M1 2l14 11L29 2" stroke="#fff" stroke-width="2" fill="none"/></svg>
    hello@havenstaff.example
  </div>
  <nav class="abs nav">
    <a class="active" style="left:260px">HOME</a>
    <a style="left:348px">ABOUT US</a>
    <a style="left:460px">SERVICES OFFERED</a>
    <a style="left:637px">PRICING</a>
    <a style="left:734px">TESTIMONIALS</a>
    <a style="left:877px">FAQS</a>
    <a style="left:952px">CONTACT US</a>
    <a style="left:1081px">BLOG</a>
  </nav>
</header>

<section>
  <div class="abs hero" role="img" aria-label="Photo of a man in a sun hat working on a laptop on a beach lounger"></div>
  <h1 class="abs hero-title"><span class="l1">VIRTUAL EMPLOYEE</span><span class="l2">RECRUITMENT SERVICES</span></h1>
  <div class="abs btn-quote">REQUEST A QUOTE</div>
  <svg class="abs arrow" style="left:64px" width="22" height="40" viewBox="0 0 22 40"><path d="M19 3L4 20l15 17" stroke="#fff" stroke-width="5" fill="none"/></svg>
  <svg class="abs arrow" style="left:1128px" width="22" height="40" viewBox="0 0 22 40"><path d="M3 3l15 17L3 37" stroke="#fff" stroke-width="5" fill="none"/></svg>
</section>

<section class="abs intro">
  <p>Tired of being stuck in your 9-5 cubicle job? Exhausted from commuting to and from the office? Want to spend more time with your family? We’ve got you covered.</p>
  <p>HavenStaff is a virtual staffing company that helps freelancers and virtual assistants find their perfect work-from-home job. We have a pool of clients from all over the world who are all looking for talented virtual assistants.</p>
</section>

<div class="abs photo-agent" role="img" aria-label="Photo of a smiling woman with a headset taking notes at a laptop"></div>
<section class="abs benefits">
  <h2>WITH HAVENSTAFF,<br>YOU GET TO:</h2>
  <ul>
    <li><svg width="14" height="14" viewBox="0 0 14 14"><circle cx="7" cy="7" r="7" fill="#fff"/><path d="M5 4l3 3-3 3" stroke="#fb840f" stroke-width="2" fill="none"/></svg>Work from the comfort of your home</li>
    <li><svg width="14" height="14" viewBox="0 0 14 14"><circle cx="7" cy="7" r="7" fill="#fff"/><path d="M5 4l3 3-3 3" stroke="#fb840f" stroke-width="2" fill="none"/></svg>Have a competitive and steady income</li>
    <li><svg width="14" height="14" viewBox="0 0 14 14"><circle cx="7" cy="7" r="7" fill="#fff"/><path d="M5 4l3 3-3 3" stroke="#fb840f" stroke-width="2" fill="none"/></svg>Achieve work-life balance</li>
    <li><svg width="14" height="14" viewBox="0 0 14 14"><circle cx="7" cy="7" r="7" fill="#fff"/><path d="M5 4l3 3-3 3" stroke="#fb840f" stroke-width="2" fill="none"/></svg>Learn new skills for free</li>
    <li><svg width="14" height="14" viewBox="0 0 14 14"><circle cx="7" cy="7" r="7" fill="#fff"/><path d="M5 4l3 3-3 3" stroke="#fb840f" stroke-width="2" fill="none"/></svg>Work with a dedicated team who can provide you with HR, payroll, IT, and training assistance 24/7!</li>
  </ul>
</section>

<section class="abs who">
  <h2>WHO ARE OUR<br>VIRTUAL ASSISTANTS?</h2>
  <div class="copy">
    <p>We have VAs from all over the Philippines.</p>
    <p>Our VA pool is composed of highly dedicated people armed with the right set of skills clients are looking for in a virtual assistant. We hire VAs of varying work experience and skill levels, and we help our VAs improve their skills so that they can get the jobs and clients they want.</p>
    <p>HavenStaff accepts VAs in a variety of niches. Currently, our VAs belongs to one or more of the following groups: Administrative VAs, eCommerce VAs, and Specialist VAs.</p>
    <p>Are you ready to join the team? To start the application process, please click on the button below.</p>
  </div>
</section>
<div class="abs photo-beach" role="img" aria-label="Photo of a woman in a straw hat working on a laptop on a sunny beach"></div>

<section>
  <h2 class="abs why-title">WHY WORK FOR HAVENSTAFF?</h2>

  <div class="abs bar left" style="top:2349px"><span class="label">COMPETITIVE<br>HOURLY RATES</span><svg width="46" height="40" viewBox="0 0 46 40" fill="none" stroke="#fff" stroke-width="2"><path d="M2 26h8v12H2zM10 28h10l12-6 4 3-14 10H10"/><text x="22" y="14" fill="#fff" stroke="none" font-size="16" font-family="Montserrat">$</text></svg></div>
  <div class="abs bar left active" style="top:2423px"><span class="label">FLEXIBLE HOURS</span><svg width="42" height="42" viewBox="0 0 42 42" fill="none" stroke="#fff" stroke-width="2"><rect x="2" y="5" width="30" height="28"/><path d="M2 12h30M8 17h6v5H8zM18 17h6v5h-6zM8 25h6v4H8z"/><circle cx="33" cy="33" r="7" fill="#1565d0"/><path d="M33 29v4h3"/></svg></div>
  <div class="abs bar left" style="top:2497px"><span class="label">FLEXIBLE SCHEDULE</span><svg width="42" height="42" viewBox="0 0 42 42" fill="none" stroke="#fff" stroke-width="2"><rect x="2" y="5" width="30" height="28"/><path d="M2 12h30M8 17h6v5H8zM18 17h6v5h-6zM8 25h6v4H8z"/><circle cx="33" cy="33" r="7" fill="#050505"/><path d="M33 29v4h3"/></svg></div>
  <div class="abs bar left" style="top:2574px"><span class="label">WEEKLY PAYOUT<br>VIA PAYWISE</span><svg width="42" height="40" viewBox="0 0 42 40" fill="none" stroke="#fff" stroke-width="2"><rect x="4" y="6" width="30" height="24" rx="3"/><path d="M4 13h30M10 22h8"/></svg></div>
  <div class="abs bar left" style="top:2648px"><span class="label">PAYWISE FEES COVERED</span><svg width="44" height="40" viewBox="0 0 44 40" fill="none" stroke="#fff" stroke-width="2"><rect x="2" y="10" width="36" height="24"/><path d="M2 28h36M8 18h10"/><circle cx="34" cy="10" r="7" fill="#050505"/><text x="30.5" y="14" fill="#fff" stroke="none" font-size="10" font-family="Montserrat">$</text></svg></div>
  <div class="abs bar left" style="top:2723px"><span class="label">FREE TRAINING &amp;<br>UPSKILLING</span><svg width="46" height="40" viewBox="0 0 46 40" fill="none" stroke="#fff" stroke-width="2"><circle cx="22" cy="9" r="6"/><path d="M2 24l20-8 20 8-20 8zM10 27v8h24v-8"/></svg></div>

  <div class="abs bar right" style="top:2349px"><svg width="40" height="44" viewBox="0 0 40 44" fill="none" stroke="#fff" stroke-width="2"><rect x="6" y="2" width="28" height="40" rx="2"/><circle cx="20" cy="13" r="5"/><path d="M12 24h16M12 30h16M12 36h10"/></svg><span class="label">PAYROLL PROCESSING</span></div>
  <div class="abs bar right" style="top:2425px"><svg width="40" height="42" viewBox="0 0 40 42" fill="none" stroke="#fff" stroke-width="2"><path d="M4 2h20l6 6v12M4 2v36"/><path d="M9 10h10M9 16h14"/><rect x="10" y="24" width="28" height="14"/><circle cx="24" cy="31" r="3"/></svg><span class="label">NO PLACEMENT OR<br>PROCESSING FEE</span></div>
  <div class="abs bar right" style="top:2500px"><svg width="42" height="42" viewBox="0 0 42 42" fill="none" stroke="#fff" stroke-width="2"><path d="M3 20L21 4l18 16M8 16v22h26V16"/><rect x="15" y="20" width="12" height="10"/><path d="M18 38v-4h6v4"/></svg><span class="label">WORK FROM HOME</span></div>
  <div class="abs bar right" style="top:2575px"><svg width="42" height="42" viewBox="0 0 42 42" fill="none" stroke="#fff" stroke-width="2"><path d="M21 3l3 6 6 1-4 4 1 6-6-3-6 3 1-6-4-4 6-1z"/><path d="M3 28h12v12H3zM15 24h12v16H15zM27 31h12v9H27z"/></svg><span class="label">VARIOUS POSITIONS<br>AVAILABLE</span></div>
  <div class="abs bar right" style="top:2651px;height:103px"><svg width="46" height="44" viewBox="0 0 46 44" fill="none" stroke="#fff" stroke-width="2"><rect x="2" y="8" width="30" height="32"/><rect x="14" y="2" width="30" height="32" fill="#050505"/><path d="M20 12h18M20 18h18M20 24h12"/></svg><span class="label">CONTINUOUS<br>RE-ASSIGNMENT<br>TO CLIENTS</span></div>

  <div class="abs circle-glow"></div>
  <div class="abs circle-ring"></div>
  <div class="abs circle-core">
    <svg width="86" height="80" viewBox="0 0 86 80" fill="none" stroke="#fff" stroke-width="3"><rect x="2" y="8" width="66" height="56"/><path d="M2 20h66M16 2v12M30 2v12M44 2v12M58 2v12M12 28h12v10H12zM30 28h12v10H30zM48 28h12v10H48zM12 44h12v10H12zM30 44h12v10H30z"/><circle cx="66" cy="60" r="16" fill="#114ea6"/><path d="M66 50v10h8"/></svg>
    <h3>FLEXIBLE HOURS</h3>
    <p>Full-time or part-time? We’ll match you with a client whose staffing needs perfectly matches your availability!</p>
  </div>
</section>

<footer class="abs footer">
  <h4 style="left:155px">CONTACT US</h4>
  <ul style="left:157px"><li>48 Harbor Lane Suite 2</li><li>Springvale 40012</li><li>(555) 014 2290</li><li>hello@havenstaff.example</li></ul>
  <h4 style="left:461px">COMPANY</h4>
  <ul style="left:462px"><li>Home</li><li>About Us</li><li>Services offered</li><li>Pricing</li><li>Testimonials</li></ul>
  <ul style="left:656px"><li>FAQs</li><li>Contact Us</li><li>Blog</li></ul>
  <h4 style="left:830px">FOLLOW US</h4>
  <div class="social" aria-label="Social links"><span></span><span></span><span></span><span></span></div>
  <div class="rule"></div>
  <p class="copyright">© 2020 HavenStaff | All Rights Reserved</p>
</footer>

</body>
</html>
```